Harbor Crestline (Business Card Design)

Need business cards designed. Something modern, chic, and sleek. Mabye the back of the card should be the navy blue that is in the logo and then just the logo on the back.

Target Market(s)

Those in the hotel, office, and renovation industry

Contact Information for Business Card

1. Logo 2. Dorian Fenwick 3. CEO/Founder 4. Phone: (833) HarbCre / (833) 427-2731 5. Email: dorian@theharborcrestline.com 6. Website: www.theharborcrestline.com

Font styles to use
Other font styles liked:
• Look at the logo font and base the font for everything else off of that.

Colors
0054AA
0677BA
7BADD7
CADEEF
E8F1F8

Requirements
Must have
• Colors that are associated in the logo
Nice to have
• Sleek modern clean and chic design.

```html
<!DOCTYPE html>
<html lang="en">
<head>
<meta charset="utf-8">
<title>Harbor Crestline — Business Card</title>
<link rel="stylesheet" href="https://fonts.googleapis.com/css2?family=Montserrat:wght@500;600&family=Open+Sans:wght@400;600;700&display=swap">
<style>
  :root {
    --backdrop: #222222;
    --navy: #0e1840;
    --gold: #d1a64a;
    --white: #ffffff;
    --card-w: 540px;
    --card-h: 310px;
    --divider-x: 250px;
  }
  * { box-sizing: border-box; margin: 0; padding: 0; }
  html, body { width: 1200px; height: 780px; overflow: hidden; background: var(--backdrop); }
  .sheet {
    width: 1200px; height: 780px;
    display: flex; align-items: center; justify-content: center; gap: 40px;
  }
  .card {
    position: relative;
    width: var(--card-w); height: var(--card-h);
    background: var(--navy);
    border-radius: 16px;
    overflow: hidden;
    box-shadow: 0 0 0 3px var(--gold), 0 18px 30px rgba(0,0,0,.55);
  }
  .wordmark {
    font-family: "Montserrat", sans-serif;
    font-weight: 600;
    color: var(--white);
    text-transform: uppercase;
    letter-spacing: .12em;
    display: flex; align-items: center; gap: 12px;
    white-space: nowrap;
  }
  .wordmark__square { width: 14px; height: 14px; background: var(--gold); flex: none; }
  .wordmark__text { display: flex; flex-direction: column; line-height: 1.1; }
  .card--back .wordmark {
    position: absolute; inset: 0; justify-content: center; font-size: 34px;
  }
  .card--front .wordmark {
    position: absolute; left: 0; top: 96px; width: var(--divider-x);
    justify-content: center; font-size: 22px; gap: 10px;
  }
  .card--front .wordmark__square { width: 12px; height: 12px; }
  .divider {
    position: absolute; left: var(--divider-x); top: 50px; width: 2px; height: 178px; background: var(--white);
  }
  .details {
    position: absolute; left: 276px; top: 52px;
    font-family: "Open Sans", sans-serif; color: var(--white);
  }
  .details__name { font-size: 27px; font-weight: 700; line-height: 1.05; }
  .details__first { color: var(--gold); }
  .details__title { font-size: 13px; font-weight: 600; margin-top: 2px; }
  .details__address { font-size: 10.5px; line-height: 1.4; margin-top: 18px; }
  .contacts { list-style: none; font-size: 10.5px; line-height: 1.55; margin-top: 14px; }
  .contacts li { display: flex; align-items: center; gap: 6px; }
  .contacts svg { width: 10px; height: 10px; flex: none; }
  .bands { position: absolute; left: 0; bottom: 0; width: 100%; height: 80px; }
</style>
</head>
<body>
<main class="sheet">
  <section class="card card--back" aria-label="Card back">
    <div class="wordmark"><span class="wordmark__square"></span><span class="wordmark__text"><span>Harbor</span><span>Crestline</span></span></div>
  </section>

  <section class="card card--front" aria-label="Card front">
    <div class="wordmark"><span class="wordmark__square"></span><span class="wordmark__text"><span>Harbor</span><span>Crestline</span></span></div>
    <div class="divider"></div>
    <div class="details">
      <h1 class="details__name"><span class="details__first">Dorian</span> Fenwick</h1>
      <p class="details__title">CEO/Founder</p>
      <p class="details__address">4170 Larkmoor Ave<br>Suite 2200, Brindale, MD 20918</p>
      <ul class="contacts">
        <li><svg viewBox="0 0 10 10"><path fill="#d1a64a" d="M2 .5l2 2-1 1.2a6 6 0 0 0 3.3 3.3L7.5 6l2 2-1.3 1.5C4.5 9.3.7 5.5.5 1.8z"/></svg>(833) HarbCre / (833) 427-2731</li>
        <li><svg viewBox="0 0 10 10"><circle cx="5" cy="5" r="4.3" fill="none" stroke="#d1a64a" stroke-width="1.2"/><path d="M.8 5h8.4M5 .7c-2.4 2.6-2.4 6 0 8.6M5 .7c2.4 2.6 2.4 6 0 8.6" fill="none" stroke="#d1a64a" stroke-width=".9"/></svg>www.theharborcrestline.com</li>
        <li><svg viewBox="0 0 10 10"><rect x=".6" y="2" width="8.8" height="6.2" fill="none" stroke="#d1a64a" stroke-width="1.1"/><path d="M.8 2.3 5 5.6l4.2-3.3" fill="none" stroke="#d1a64a" stroke-width="1.1"/></svg>dorian@theharborcrestline.com</li>
      </ul>
    </div>
    <svg class="bands" viewBox="0 0 540 80" preserveAspectRatio="none" aria-hidden="true">
      <polygon points="0,56 300,56 288,70 0,70" fill="#d1a64a"/>
      <polygon points="312,42 540,42 540,56 300,56" fill="#ffffff"/>
      <rect x="294" y="43" width="14" height="14" fill="#0e1840" stroke="#ffffff" stroke-width="2"/>
    </svg>
  </section>
</main>
</body>
</html>
```